Brightfen Business Card Redesign & Logo Update

We need to update our business cards to something more modern and fresh. Brightfen can provide the current color schemes and old design examples, but welcome creativity in helping us with this redesign. PLEASE NOTE that we no longer utilize the "tree" and/or "leaf" imagery in our branding. If able would apprecaite an update on the quality of our "words only" logo in Ai. / PNG formats too.

Target Market(s)

Investors, landowners, corporate partners, contractors

Industry/Entity Type

Environmental Restoration & Conservation

Contact Information for Business Card

Logo, persons name, title, mailing address, phone and email, website url

Font styles to use
Other font styles liked:
• Merriweather

Requirements
Nice to have
• Logo, persons name, title, mailing address, phone and email, website url, but open to ideams
Should not have
• No all back backgrounds

```html
<!DOCTYPE html>
<html lang="en">
<head>
<meta charset="UTF-8">
<title>Brightfen Business Card</title>
<link href="https://fonts.googleapis.com/css2?family=Oswald:wght@700&family=Open+Sans:wght@400;700&display=swap" rel="stylesheet">
<style>
  :root {
    --bg: #e6e8e5;
    --card: #ffffff;
    --green: #15803f;
    --orange: #ee7d22;
    --ink: #1c1c1c;
  }
  html, body {
    margin: 0;
    width: 1200px;
    height: 780px;
    overflow: hidden;
    background: var(--bg);
  }
  .canvas {
    position: relative;
    width: 1200px;
    height: 780px;
  }
  .card {
    position: absolute;
    top: 100px;
    width: 330px;
    height: 580px;
    background: var(--card);
    box-shadow: 0 8px 22px rgba(0,0,0,0.18);
    overflow: hidden;
  }
  .card--front {
    left: 235px;
    border-radius: 80px 0 80px 0;
  }
  .card--back {
    left: 635px;
    border-radius: 0 80px 0 80px;
  }
  .front-wordmark {
    position: absolute;
    left: 50%;
    top: 50%;
    transform: translate(-50%, -50%) rotate(-90deg);
    font-family: "Oswald", sans-serif;
    font-weight: 700;
    font-size: 104px;
    letter-spacing: 4px;
    line-height: 1;
    color: var(--green);
    white-space: nowrap;
  }
  .back-wordmark {
    position: absolute;
    top: 48px;
    left: 0;
    right: 0;
    text-align: center;
    font-family: "Oswald", sans-serif;
    font-weight: 700;
    font-size: 50px;
    letter-spacing: 2px;
    line-height: 1;
    color: var(--green);
  }
  .identity {
    position: absolute;
    left: 0;
    right: 0;
    top: 330px;
    text-align: center;
    font-family: "Open Sans", sans-serif;
  }
  .identity__name {
    margin: 0;
    font-size: 25px;
    font-weight: 700;
    line-height: 1.1;
  }
  .identity__first { color: var(--orange); }
  .identity__last { color: var(--green); }
  .identity__title {
    margin: 4px 0 0;
    font-size: 16px;
    color: var(--ink);
  }
  .divider {
    display: block;
    margin: 10px auto 0;
  }
  .contact-icons {
    display: flex;
    justify-content: center;
    gap: 14px;
    margin-top: 4px;
  }
  .contact-list {
    list-style: none;
    margin: 10px 0 0;
    padding: 0;
    font-size: 14px;
    line-height: 1.45;
    color: var(--ink);
  }
</style>
</head>
<body>
<main class="canvas">
  <section class="card card--front" aria-label="Card front">
    <div class="front-wordmark">BRIGHTFEN</div>
  </section>

  <section class="card card--back" aria-label="Card back">
    <div class="back-wordmark">BRIGHTFEN</div>

    <div class="identity">
      <h1 class="identity__name"><span class="identity__first">Mara</span> <span class="identity__last">Kovanek</span></h1>
      <p class="identity__title">Founder</p>

      <svg class="divider" width="270" height="14" viewBox="0 0 270 14" aria-hidden="true">
        <path d="M150 7 L268 4 L268 6 Z" fill="var(--green)"/>
        <path d="M150 7 L268 10 L268 8 Z" fill="var(--green)"/>
        <g fill="var(--green)" font-family="sans-serif" font-size="10">
          <text x="118" y="11">★★★</text>
        </g>
      </svg>

      <div class="contact-icons" aria-hidden="true">
        <svg width="30" height="30" viewBox="0 0 30 30">
          <circle cx="15" cy="15" r="13" fill="none" stroke="var(--green)" stroke-width="2"/>
          <circle cx="15" cy="15" r="10" fill="var(--orange)"/>
          <path d="M11 10 q-1 6 8 10 l1.5-2 -2.5-2 -1.5 1 q-2-1-3-3 l1-1.5 -2-2.5z" fill="#fff"/>
        </svg>
        <svg width="30" height="30" viewBox="0 0 30 30">
          <circle cx="15" cy="15" r="13" fill="none" stroke="var(--green)" stroke-width="2"/>
          <circle cx="15" cy="15" r="10" fill="var(--orange)"/>
          <rect x="9.5" y="11" width="11" height="8" fill="none" stroke="#fff" stroke-width="1.4"/>
          <path d="M9.5 11 L15 15.5 L20.5 11" fill="none" stroke="#fff" stroke-width="1.4"/>
        </svg>
        <svg width="30" height="30" viewBox="0 0 30 30">
          <circle cx="15" cy="15" r="13" fill="none" stroke="var(--green)" stroke-width="2"/>
          <circle cx="15" cy="15" r="10" fill="var(--orange)"/>
          <circle cx="15" cy="15" r="5.5" fill="none" stroke="#fff" stroke-width="1.3"/>
          <ellipse cx="15" cy="15" rx="2.3" ry="5.5" fill="none" stroke="#fff" stroke-width="1.1"/>
          <line x1="9.5" y1="15" x2="20.5" y2="15" stroke="#fff" stroke-width="1.1"/>
        </svg>
      </div>

      <ul class="contact-list">
        <li>(555) 214-0386</li>
        <li>info@brightfen.co</li>
        <li>www.brightfen.co</li>
      </ul>

      <svg class="divider" width="270" height="14" viewBox="0 0 270 14" aria-hidden="true">
        <path d="M120 7 L2 4 L2 6 Z" fill="var(--green)"/>
        <path d="M120 7 L2 10 L2 8 Z" fill="var(--green)"/>
        <g fill="var(--green)" font-family="sans-serif" font-size="10">
          <text x="124" y="11">★★★</text>
        </g>
      </svg>
    </div>
  </section>
</main>
</body>
</html>
```